Brenlow Estates Website and Logo Design

We need a new logo and website designed for 'Brenlow Estates Ltd', which is a well established Guernsey property holding company founded in 1934.

The company does not currently have a website. The new website should be similar in style and layout to https://www.quorvanhall.example/.

Target Market(s)

Industry, Media, Tenants

Industry/Entity Type

Property Management

Logo Text

BEL OR Brenlow Estates Ltd OR BE

Coding

Coded - Design and coding required

Number of Pages Required

4 page

Font styles to use
Other font styles liked:
• Helvetica

Requirements
Must have
• The logo laying over the picture (like https://www.quorvanhall.example/).
• Big pictures on homepage (like https://www.quorvanhall.example/)

```html
<!DOCTYPE html>
<html lang="en">
<head>
<meta charset="utf-8">
<title>Brenlow Estates Ltd</title>
<link rel="stylesheet" href="https://fonts.googleapis.com/css2?family=Oswald:wght@400;500&family=Open+Sans:wght@400;600&family=Dancing+Script:wght@500&display=swap">
<style>
:root{
  --accent:#21bcbc;
  --accent-dark:#179a9a;
  --ink:#222628;
  --text:#5c6266;
  --muted:#8c9296;
  --dark:#2b2e31;
  --darker:#1f2124;
  --light:#f3f4f5;
  --white:#ffffff;
  --line:#d9dcdf;
}
*{box-sizing:border-box;margin:0;padding:0}
html,body{width:1200px;height:4292px;overflow:hidden}
body{font-family:"Open Sans",Arial,sans-serif;color:var(--text);background:var(--white);position:relative}
section,header,footer,nav{position:absolute;left:0;width:1200px}
.heading{font-family:"Oswald",Arial,sans-serif;font-weight:500;font-size:44px;color:var(--ink);text-align:center;text-transform:uppercase;letter-spacing:1px}
.heading span{color:var(--accent)}
.heading.light{color:var(--white)}
.script{font-family:"Dancing Script",cursive;font-size:26px;color:var(--ink);text-align:center}
.script.light{color:var(--white)}
.btn{display:inline-block;background:var(--accent);color:var(--white);font-family:"Oswald",Arial,sans-serif;font-size:17px;letter-spacing:1px;text-transform:uppercase;padding:14px 30px;text-decoration:none}
.photo{position:absolute}

/* hero */
.hero{top:0;height:620px;overflow:hidden}
.hero .photo{inset:0;background:linear-gradient(180deg,#3f6fb4 0%,#7ea4d6 26%,#c9c7bd 46%,#9b8f80 58%,#2f6b78 72%,#3c8a96 100%)}
.brand-name{position:absolute;top:112px;left:0;width:1200px;text-align:center;font-family:"Oswald",Arial,sans-serif;font-weight:500;font-size:54px;color:var(--white);text-transform:uppercase;letter-spacing:2px;line-height:1}

/* nav */
.main-nav{top:620px;height:52px;background:var(--darker);display:flex;justify-content:center}
.main-nav a{font-family:"Oswald",Arial,sans-serif;font-size:16px;color:var(--white);text-decoration:none;line-height:52px;padding:0 28px;text-transform:uppercase}
.main-nav a.active{color:var(--accent)}
.main-nav a+a{border-left:1px solid #3c3f43}

/* about */
.about{top:672px;height:376px;text-align:center;padding-top:52px}
.about p.body{width:820px;margin:26px auto 30px;font-size:15px;line-height:24px}

/* why */
.why{top:1048px;height:632px;overflow:hidden}
.why .photo{inset:0;background:linear-gradient(180deg,#2c2f33 0%,#3a3e44 14%,#4a4f52 40%,#3b3d3f 70%,#24272a 100%)}
.why .heading{position:absolute;top:54px;width:100%}
.why-cols{position:absolute;top:176px;left:140px;width:920px;display:flex;justify-content:space-between}
.why-col{width:270px;text-align:center;color:var(--white)}
.why-col h3{font-family:"Oswald",Arial,sans-serif;font-weight:400;font-size:30px;text-transform:uppercase}
.why-col .thumb{width:164px;height:164px;border-radius:50%;border:4px solid var(--white);margin:18px auto 20px}
.why-col p{font-size:14px;line-height:22px;color:#e3e5e7}
.why-actions{position:absolute;top:540px;width:100%;display:flex;justify-content:center;gap:14px}

/* work */
.work{top:1680px;height:648px;text-align:center;padding-top:54px}
.work .script{margin-top:4px}
.filters{display:flex;justify-content:center;gap:10px;margin-top:18px}
.filters span{font-size:13px;border:1px solid var(--line);padding:5px 14px;color:var(--text)}
.filters span.active{background:var(--dark);color:var(--white);border-color:var(--dark)}
.work-grid{position:absolute;left:80px;top:216px;width:1040px;display:grid;grid-template-columns:repeat(4,1fr);grid-template-rows:168px 180px;gap:20px}
.tile{position:relative}
.tile-label{position:absolute;inset:0;background:rgba(20,22,24,.55);display:flex;align-items:center;justify-content:center;font-family:"Oswald",Arial,sans-serif;font-size:20px;color:var(--white)}

/* testimonial */
.clients-title{top:2328px;height:132px;background:var(--dark);display:flex;align-items:center;justify-content:center}
.clients{top:2460px;height:372px;overflow:hidden;text-align:center}
.clients .photo{inset:0;background:linear-gradient(180deg,#5e7b94 0%,#3f5a70 40%,#2d3c47 70%,#1f2a31 100%)}
.quote{position:absolute;top:60px;left:0;width:100%;font-family:"Oswald",Arial,sans-serif;font-size:26px;line-height:40px;color:var(--white);text-transform:uppercase;letter-spacing:1px}
.author{position:absolute;top:198px;width:100%;font-size:16px;color:var(--white)}
.arrows{position:absolute;top:262px;width:100%;display:flex;justify-content:center;gap:12px}
.arrows span{width:34px;height:34px;border-radius:50%;background:rgba(255,255,255,.25);display:flex;align-items:center;justify-content:center}

/* blog */
.blog{top:2832px;height:600px;padding-top:64px;text-align:center}
.posts{position:absolute;top:180px;left:80px;width:1040px;display:flex;justify-content:space-between;text-align:left}
.post{width:334px}
.post .thumb{height:152px;position:relative}
.post h4{font-size:17px;font-weight:400;color:var(--accent);line-height:24px;margin-top:14px}
.post .meta{font-size:11px;color:var(--muted);margin:8px 0 12px}
.post p{font-size:13px;line-height:20px}
.post .more{display:block;font-size:13px;color:var(--accent);margin-top:12px;text-decoration:none}

/* contact form */
.enquiry{top:3432px;height:540px;overflow:hidden}
.enquiry .photo{inset:0;background:linear-gradient(120deg,#c7b6a2 0%,#8a8fa0 40%,#c8c2bb 70%,#6f5e52 100%)}
.enquiry .veil{position:absolute;inset:0;background:rgba(30,33,36,.45)}
.enquiry .heading{position:absolute;top:44px;width:100%}
.enquiry .script{position:absolute;top:108px;width:100%}
.form{position:absolute;top:160px;left:100px;width:1012px;height:340px;border:2px solid rgba(255,255,255,.7)}
.field{position:absolute;left:0;width:420px;height:40px;background:rgba(255,255,255,.85);font-size:14px;color:var(--muted);padding:10px 14px}
.message{position:absolute;left:492px;top:56px;width:520px;height:152px;border:2px solid rgba(255,255,255,.85);font-size:14px;color:var(--white);padding:10px 14px}
.form .btn{position:absolute;top:250px;left:436px}

/* contact info */
.contact{top:3972px;height:276px;background:var(--dark);text-align:center;padding-top:22px}
.socials{display:flex;justify-content:center;gap:8px;margin-top:38px}
.socials span{width:34px;height:34px;background:#5b6066}
.socials span:first-child{background:var(--accent)}
.contact p{font-size:13px;color:#c5c9cc;line-height:22px}
.contact p:first-of-type{margin-top:26px}
.contact p a{color:var(--accent);text-decoration:none}
.site-footer{top:4248px;height:44px;background:var(--darker);text-align:center;font-size:12px;color:#9aa0a4;line-height:44px}
.site-footer span{color:var(--accent)}
</style>
</head>
<body>

<header class="hero">
  <div class="photo" role="img" aria-label="Harbour view with boats and waterfront houses under a blue sky"></div>
  <div class="brand-name">Brenlow Estates Ltd</div>
</header>

<nav class="main-nav">
  <a class="active" href="#">Home</a><a href="#">About</a><a href="#">Projects</a><a href="#">News</a><a href="#">Contact</a>
</nav>

<section class="about">
  <h2 class="heading">About <span>Brenlow Estates Ltd</span></h2>
  <div class="script">Everything You may want to know</div>
  <p class="body">Brenlow Estates Limited (BEL) is a family owned Guernsey property holding company. It purchases properties that are considered to have potential for development either through refurbishment or by obtaining planning permission to change its classification from, for example, industrial or retail to offices or residential, or by the marriage value of buying an adjacent property to one already owned by BEL.</p>
  <a class="btn" href="#">Read More</a>
</section>

<section class="why">
  <div class="photo" role="img" aria-label="Darkened view over a Guernsey town and harbour"></div>
  <h2 class="heading light">Why <span>Guernsey?</span></h2>
  <div class="why-cols">
    <div class="why-col">
      <h3>Yesterday</h3>
      <div class="thumb" role="img" aria-label="Sunset over the island coastline" style="background:linear-gradient(180deg,#f2b25a,#b8643a)"></div>
      <p>BEL was founded in 1934 by its founder to manage with his own extensive investments and the property portfolio in Guernsey.</p>
    </div>
    <div class="why-col">
      <h3>Today</h3>
      <div class="thumb" role="img" aria-label="Stone town house on a quiet street" style="background:linear-gradient(180deg,#9fb7cf,#8a7a66)"></div>
      <p>The family now has steadily built on these foundations and the fourth and sixth generation elements now manage the company operations in the fold.</p>
    </div>
    <div class="why-col">
      <h3>Tomorrow</h3>
      <div class="thumb" role="img" aria-label="Modern house with large windows at dusk" style="background:linear-gradient(180deg,#5e6f7e,#c9a46e)"></div>
      <p>In keeping with its past property development philosophy, its intimate understanding of the local property market and BEL successful management are dedicated to the younger generation.</p>
    </div>
  </div>
  <div class="why-actions"><a class="btn" href="#">Read More</a><a class="btn" href="#">Contact Now</a></div>
</section>

<section class="work">
  <h2 class="heading">Our Recent <span>Work</span></h2>
  <div class="script">Check Out a List of Our Projects</div>
  <div class="filters"><span class="active">All</span><span>Property For Sale</span><span>Property For Rent</span></div>
  <div class="work-grid">
    <div class="tile" role="img" aria-label="Bedroom interior of a property for sale" style="background:linear-gradient(135deg,#6b5a4a,#c7b59d)"><div class="tile-label">6 Bed Property For SALE</div></div>
    <div class="tile" role="img" aria-label="Glass office building interior" style="background:linear-gradient(135deg,#4f8fc4,#d6e6f2)"></div>
    <div class="tile" role="img" aria-label="Apartment block under blue sky" style="background:linear-gradient(135deg,#7fa9d4,#c9b79a)"></div>
    <div class="tile" role="img" aria-label="Villa with pool at dusk" style="background:linear-gradient(135deg,#3d4f6f,#d58a5a)"></div>
    <div class="tile" role="img" aria-label="White modern house with pool" style="background:linear-gradient(135deg,#9cc7e8,#eef2f4)"></div>
    <div class="tile" role="img" aria-label="Grey contemporary house on a lawn" style="background:linear-gradient(135deg,#4f84c0,#6f8a64)"></div>
    <div class="tile" role="img" aria-label="Seafront buildings with harbour" style="background:linear-gradient(135deg,#6fa7d6,#b89c7c)"></div>
    <div class="tile" role="img" aria-label="Open plan living room" style="background:linear-gradient(135deg,#a37d5a,#e6d2b4)"></div>
  </div>
</section>

<section class="clients-title"><h2 class="heading light">What <span>Clients</span> Say</h2></section>
<section class="clients">
  <div class="photo" role="img" aria-label="Rocky coastline with a lighthouse at dusk"></div>
  <p class="quote">" Lorem Ipsum is simply dummy text of the printing<br>and typesetting industry. "</p>
  <p class="author">Marcus Avery</p>
  <div class="arrows">
    <span><svg width="12" height="12" viewBox="0 0 12 12"><path d="M8 1 3 6l5 5" fill="none" stroke="#fff" stroke-width="2"/></svg></span>
    <span><svg width="12" height="12" viewBox="0 0 12 12"><path d="M4 1l5 5-5 5" fill="none" stroke="#fff" stroke-width="2"/></svg></span>
  </div>
</section>

<section class="blog">
  <h2 class="heading">We Are Always Doing <span>Something</span></h2>
  <div class="script">Check Out Our Latest Blog Posts</div>
  <div class="posts">
    <article class="post">
      <div class="thumb" role="img" aria-label="Aerial view of a coastal town" style="background:linear-gradient(135deg,#3f8fa8,#c9b08a)"></div>
      <h4>Lorem ipsum is simply dummy text of the printing and typesetting</h4>
      <div class="meta">Admin &nbsp; 12 May 2016 &nbsp; 3 Comments</div>
      <p>Lorem ipsum is simply dummy text of the printing and typesetting industry. Lorem Ipsum has been the industry's standard dummy text.</p>
      <a class="more" href="#">READ MORE »</a>
    </article>
    <article class="post">
      <div class="thumb" role="img" aria-label="Aerial view of a coastal town" style="background:linear-gradient(135deg,#3f8fa8,#c9b08a)"><div class="tile-label">Read The Full Article</div></div>
      <h4>Lorem ipsum is simply dummy text of the printing and typesetting</h4>
      <div class="meta">Admin &nbsp; 12 May 2016 &nbsp; 3 Comments</div>
      <p>Lorem ipsum is simply dummy text of the printing and typesetting industry. Lorem Ipsum has been the industry's standard dummy text.</p>
      <a class="more" href="#">READ MORE »</a>
    </article>
    <article class="post">
      <div class="thumb" role="img" aria-label="Aerial view of a coastal town" style="background:linear-gradient(135deg,#3f8fa8,#c9b08a)"></div>
      <h4>Lorem ipsum is simply dummy text of the printing and typesetting</h4>
      <div class="meta">Admin &nbsp; 12 May 2016 &nbsp; 3 Comments</div>
      <p>Lorem ipsum is simply dummy text of the printing and typesetting industry. Lorem Ipsum has been the industry's standard dummy text.</p>
      <a class="more" href="#">READ MORE »</a>
    </article>
  </div>
</section>

<section class="enquiry">
  <div class="photo" role="img" aria-label="Business meeting around a table with documents"></div>
  <div class="veil"></div>
  <h2 class="heading light">There's No Better <span>Time</span> Than Now</h2>
  <div class="script light">Get in touch, let's work together</div>
  <div class="form">
    <div class="field" style="top:56px">Name</div>
    <div class="field" style="top:112px">E-Mail</div>
    <div class="field" style="top:168px">Phone</div>
    <div class="message">Message</div>
    <a class="btn" href="#">Contact Us</a>
  </div>
</section>

<section class="contact">
  <h2 class="heading light">Contact <span>Us</span></h2>
  <div class="socials"><span></span><span></span><span></span><span></span><span></span></div>
  <p>01481 555 0134 | <a href="#">info@brenlowestates.example</a></p>
  <p>123 Building Name, Street Name, City, Country Zipcode</p>
</section>

<footer class="site-footer">© <span>BRENLOW ESTATES LTD</span> 2016. All Rights Reserved.</footer>

</body>
</html>
```